House-share and Room Rental Website (With Focus on the Bedroom Landing Page)

Looking for website design for our House-share (executive accommodation) and room rental business.

Our company name is: Lodgivo could also be written as LodGivo or lodgivo. Either is fine .. just looking for a nice clean catchy logo to go with the design.

EXAMPLES
These are examples of other websites in this field that are doing well. this is a kind of baseline.
https://nestpartners-example.com.au/
https://www.bunkora-example.com/
https://www.dwelzy-example.com/
https://www.habiquo-example.net/
https://www.cohabiscout-example.com.au/

Our business model is to rent rooms to people looking for high-quality accommodation. We fill the gap between those looking to rent rooms and those with rooms to rent. However, our model is slightly different from those already on the market as we looking to fill a massive gap in the market delivering upmarket rooms for rent.(Executive Accommodation) also in the back end will be coupled with a self management process in the back end.

We offer executive style accommodation that stands out above the rest. With special extras like fire safety.. and management processes that create happier homes. We are looking for a web design package that can help us grow and scale our business. We need a design that is captivating

Our MAIN focus is having a room landing page that stands out from the rest... The core of our business will rely on the promotion of the rooms in a share house... so the whole design relies on the BEDROOM landing page to drive results.

Target Market(s)

We have 2 markets we are aiming at ... the first market is people offering rooms to rent who want the highest rental return. The second market is people looking to rent safe, high-quality rooms, in houses that are well managed and looked after.

Industry/Entity Type

Share Economy

Logo Text

LodGivo

Number of Pages Required

5+ page

Font styles to use
Sans Serif

Colors
3276b5

Requirements
Must have
• A messaging system whereby we can create direct communication between those offering rooms and those looking for rooms.
• A call to action that says " Schedule an Inspection"
• Landing page for promoting rooms
• A home page for showing stock.
• Profile page for those selling rooms
• Profile page for those looking for rooms.
• A scheduling calendar for booking inspections
Nice to have
• Pages where new residents can lock in a room.. pay bond and rents.. and sign contracts
• Notifications
• SMS capabilities in the backend.
Should not have
• No script or handwriting fonts.

```html
<!DOCTYPE html>
<html lang="en">
<head>
<meta charset="utf-8">
<title>LodGivo – House-Share and Room Rental</title>
<link href="https://fonts.googleapis.com/css2?family=Marcellus&family=Lato:wght@400;700;900&display=swap" rel="stylesheet">
<style>
:root{
  --blue:#3276b5;
  --blue-dark:#245a8e;
  --ink:#2b2b2b;
  --muted:#8a8a8a;
  --line:#e3e3e3;
  --paper:#ffffff;
  --footer:#1f2a36;
}
*{box-sizing:border-box;margin:0;padding:0}
html,body{width:1200px;height:5070px;overflow:hidden;background:var(--paper)}
body{position:relative;font-family:'Lato',sans-serif;color:var(--ink)}
.abs{position:absolute}

/* top bar */
.topbar{left:0;top:0;width:1200px;height:40px;font-size:13px;color:#555}
.topbar .contact{left:110px;top:12px;display:flex;gap:22px}
.topbar svg{vertical-align:-2px;margin-right:6px}
.cta-inspect{right:110px;top:0;width:330px;height:40px;background:var(--blue);color:#fff;font-weight:700;font-size:15px;letter-spacing:.5px;display:flex;align-items:center;justify-content:center;gap:10px;clip-path:polygon(8% 0,100% 0,92% 100%,0 100%);text-transform:uppercase}

/* nav */
.nav{left:0;top:40px;width:1200px;height:102px}
.brand{left:110px;top:26px;font-family:'Lato',sans-serif;font-weight:700;font-size:36px;color:var(--blue);letter-spacing:.5px;line-height:48px}
.menu{right:110px;top:38px;display:flex;gap:26px;font-size:17px;color:#333;align-items:center}

/* hero */
.hero{left:0;top:142px;width:1200px;height:640px}
.hero-photo{position:absolute;inset:0;background:linear-gradient(180deg,#6f6a64 0%,#8c8781 45%,#bdb8b1 80%,#9a958e 100%)}
.hero-shade{position:absolute;inset:0;background:rgba(30,30,30,.35)}
.hero h1{position:absolute;left:0;width:1200px;top:150px;text-align:center;color:#fff;font-family:'Marcellus',serif;font-weight:400;font-size:62px;line-height:82px;letter-spacing:1px}
.hero .btn{left:502px;top:362px}
.arrow{width:48px;height:48px;border-radius:50%;background:rgba(255,255,255,.35);display:flex;align-items:center;justify-content:center}
.hero .prev{left:45px;top:268px}
.hero .next{right:45px;top:268px;background:transparent}
.hero-cut{position:absolute;left:0;bottom:0;width:1200px;height:100px}

.btn{position:absolute;background:var(--blue);color:#fff;font-weight:700;font-size:15px;letter-spacing:.5px;height:44px;border-radius:22px;display:flex;align-items:center;justify-content:center;gap:8px;text-transform:uppercase;width:196px}
.btn-outline{background:#fff;color:var(--blue);border:2px solid var(--blue)}

/* section headings */
.heading{position:absolute;left:0;width:1200px;text-align:center;font-family:'Marcellus',serif;font-weight:400;font-size:40px;color:var(--ink);letter-spacing:1px}
.heading span{color:var(--blue)}
.heading-rule{position:absolute;left:570px;width:60px;height:3px;background:var(--blue)}
.ghost{position:absolute;font-family:'Marcellus',serif;font-size:96px;color:rgba(0,0,0,.05);white-space:nowrap;letter-spacing:2px}

/* advantages */
.adv{position:absolute;top:1020px;width:300px;text-align:center}
.adv .icon{margin:0 auto;width:140px;height:140px;display:block}
.adv h3{margin-top:28px;font-size:16px;font-weight:900;letter-spacing:.3px;text-transform:uppercase}
.adv p{margin:12px auto 0;width:280px;font-size:13px;line-height:22px;color:var(--muted)}

/* about */
.about{left:0;top:1520px;width:1200px;height:880px}
.about-photo{position:absolute;left:0;top:0;width:1200px;height:880px;background:linear-gradient(100deg,#e8e8e8 0%,#f2f2f2 50%,#fafafa 75%,#ffffff 100%)}
.about h2{position:absolute;left:210px;top:230px;font-family:'Marcellus',serif;font-weight:400;font-size:42px}
.about h2 span{color:var(--blue)}
.about p{position:absolute;left:118px;top:340px;width:505px;font-size:13px;line-height:28px;color:#555;text-align:center}
.about .btn{left:450px;top:582px}
.circle{position:absolute;border-radius:50%;border:6px solid #fff;box-shadow:0 4px 14px rgba(0,0,0,.15)}

/* portfolio */
.tile{position:absolute;border-radius:14px;box-shadow:0 6px 18px rgba(0,0,0,.12)}
.zoom{position:absolute;left:100px;top:84px}

/* testimonials */
.testi{left:0;top:3380px;width:1200px;height:880px}
.testi-photo{position:absolute;inset:0;background:linear-gradient(110deg,#2f6fab 0%,#3276b5 45%,#4a86bd 75%,#3a79b2 100%);clip-path:polygon(0 12%,50% 0,100% 12%,100% 86%,50% 100%,0 86%)}
.testi .heading{color:#fff;top:262px;font-size:40px}
.testi .ghost{color:rgba(255,255,255,.1);left:262px;top:300px;font-size:96px}
.testi .heading-rule{background:#fff;top:328px}
.card{position:absolute;top:450px;width:294px;height:182px;background:#fff;text-align:center;padding-top:58px}
.card .avatar{position:absolute;left:117px;top:-30px;width:60px;height:60px;border-radius:50%;border:3px solid #fff;background:linear-gradient(180deg,#c9b6a6,#8d7866)}
.card p{font-size:14px;font-style:italic;line-height:22px;color:#333;padding:0 28px}
.card .badge{margin:8px auto 0;width:70px;height:24px;border-radius:4px;background:#e6e6e6}
.testi .arrow{top:515px;border:2px solid #fff;background:transparent;width:44px;height:44px}

/* newsletter */
.sub{position:absolute;left:0;width:1200px;text-align:center}
.input{left:338px;top:4553px;width:382px;height:46px;border:1px solid #ccc;font-size:13px;color:#777;padding:14px 22px}
.subscribe{left:728px;top:4553px;width:132px;height:46px;background:var(--blue);color:#fff;font-weight:700;font-size:14px;display:flex;align-items:center;justify-content:center}

/* contact row */
.info{position:absolute;top:4790px;display:flex;align-items:center;gap:22px;font-weight:700;font-size:15px;color:#222}
.diamond{width:58px;height:58px;display:flex;align-items:center;justify-content:center;background:#fff;box-shadow:0 3px 12px rgba(0,0,0,.12);transform:rotate(45deg)}
.diamond svg{transform:rotate(-45deg)}

.footer-links{left:0;top:4958px;width:1200px;display:flex;justify-content:center;gap:28px;font-size:15px;color:#222;letter-spacing:.5px}
.footer-links i{font-style:normal;color:#999}
.footer-bar{left:80px;top:5022px;width:1040px;height:48px;background:var(--footer);clip-path:polygon(3% 0,97% 0,100% 100%,0 100%);color:#fff;font-size:13px;display:flex;align-items:center;justify-content:center}
</style>
</head>
<body>

<!-- top bar -->
<div class="abs topbar">
  <div class="abs contact">
    <span><svg width="12" height="12" viewBox="0 0 24 24" fill="#3276b5"><path d="M6.6 10.8a15 15 0 0 0 6.6 6.6l2.2-2.2c.3-.3.7-.4 1-.2 1.1.4 2.3.6 3.6.6.6 0 1 .4 1 1V20c0 .6-.4 1-1 1A17 17 0 0 1 3 4c0-.6.4-1 1-1h3.5c.6 0 1 .4 1 1 0 1.3.2 2.5.6 3.6.1.3 0 .7-.2 1z"/></svg>1 888 888 8888</span>
    <span><svg width="13" height="11" viewBox="0 0 24 18" fill="#3276b5"><path d="M0 0h24v18H0z"/><path d="M0 0l12 9 12-9" stroke="#fff" stroke-width="2" fill="none"/></svg>info@companyname.com</span>
  </div>
  <div class="abs cta-inspect">
    <svg width="16" height="16" viewBox="0 0 24 24" fill="none" stroke="#fff" stroke-width="2"><rect x="3" y="5" width="18" height="16" rx="2"/><path d="M3 10h18M8 3v4M16 3v4"/></svg>
    Schedule an Inspection
  </div>
</div>

<!-- nav -->
<header class="abs nav">
  <div class="abs brand">LodGivo</div>
  <nav class="abs menu">
    <span>Home</span><span>About us</span><span>Services</span><span>Portfolio</span><span>News</span><span>Contact us</span>
    <svg width="16" height="16" viewBox="0 0 24 24" fill="none" stroke="#3276b5" stroke-width="3"><circle cx="10" cy="10" r="7"/><path d="M15 15l6 6"/></svg>
  </nav>
</header>

<!-- hero -->
<section class="abs hero">
  <div class="hero-photo" role="img" aria-label="Bright living room with white sofa, floor lamp and wall clock"></div>
  <div class="hero-shade"></div>
  <h1>HOUSE-SHARE AND<br>ROOM RENTAL BUSINESS</h1>
  <div class="btn">Get Started
    <svg width="14" height="14" viewBox="0 0 24 24"><circle cx="12" cy="12" r="11" fill="#fff"/><path d="M10 7l5 5-5 5" stroke="#3276b5" stroke-width="3" fill="none"/></svg>
  </div>
  <div class="abs arrow prev"><svg width="16" height="16" viewBox="0 0 24 24"><path d="M15 5l-7 7 7 7" stroke="#fff" stroke-width="3" fill="none"/></svg></div>
  <div class="abs arrow next"><svg width="16" height="16" viewBox="0 0 24 24"><path d="M9 5l7 7-7 7" stroke="#fff" stroke-width="3" fill="none"/></svg></div>
  <svg class="hero-cut" viewBox="0 0 1200 100" preserveAspectRatio="none">
    <polygon points="0,70 600,100 0,100" fill="#fff"/>
    <polygon points="780,30 1200,80 1200,100 600,100" fill="#fff"/>
    <polyline points="780,30 1200,80" stroke="#3276b5" stroke-width="6" fill="none"/>
  </svg>
</section>

<!-- advantages -->
<div class="ghost" style="left:288px;top:830px">ADVANTAGES</div>
<h2 class="heading" style="top:860px">GREAT <span>ADVANTAGES</span></h2>
<div class="heading-rule" style="top:935px"></div>

<div class="adv" style="left:100px">
  <svg class="icon" viewBox="0 0 140 140"><rect x="28" y="28" width="84" height="84" transform="rotate(45 70 70)" fill="#fff" stroke="#ccc" stroke-width="2"/>
    <circle cx="70" cy="62" r="14" fill="#3276b5"/><circle cx="70" cy="62" r="6" fill="#fff"/><path d="M60 74l-6 18 8-4 4 7 4-15M80 74l6 18-8-4-4 7-4-15" fill="#3276b5"/></svg>
  <h3>Quality Assured</h3>
  <p>Lorem ipsum dolor sit amet consectetur adipi cing elit, sed do eiusmod tempor incididunt ut labore et dolore magna aliqua.</p>
</div>
<div class="adv" style="left:450px">
  <svg class="icon" viewBox="0 0 140 140"><rect x="28" y="28" width="84" height="84" transform="rotate(45 70 70)" fill="#fff" stroke="#ccc" stroke-width="2"/>
    <path d="M50 70l20-18 20 18v22H50z" fill="#3276b5"/><rect x="64" y="76" width="12" height="16" fill="#fff"/></svg>
  <h3>High Quality Accommodation</h3>
  <p>Lorem ipsum dolor sit amet consectetur adipi cing elit, sed do eiusmod tempor incididunt ut labore et dolore magna aliqua.</p>
</div>
<div class="adv" style="left:800px">
  <svg class="icon" viewBox="0 0 140 140"><rect x="28" y="28" width="84" height="84" transform="rotate(45 70 70)" fill="#fff" stroke="#ccc" stroke-width="2"/>
    <circle cx="70" cy="70" r="20" fill="#3276b5"/><path d="M60 70l7 7 13-14" stroke="#fff" stroke-width="4" fill="none"/></svg>
  <h3>We Care, You Happy</h3>
  <p>Lorem ipsum dolor sit amet consectetur adipi cing elit, sed do eiusmod tempor incididunt ut labore et dolore magna aliqua.</p>
</div>
<div class="btn btn-outline" style="left:498px;top:1374px;width:204px">View More
  <svg width="14" height="14" viewBox="0 0 24 24"><circle cx="12" cy="12" r="11" fill="#3276b5"/><path d="M10 7l5 5-5 5" stroke="#fff" stroke-width="3" fill="none"/></svg>
</div>

<!-- about -->
<section class="abs about">
  <div class="about-photo" role="img" aria-label="Faded interior of a furnished share-house lounge"></div>
  <svg class="abs" style="left:0;top:0" width="1200" height="880" viewBox="0 0 1200 880">
    <polygon points="0,0 0,20 560,0" fill="#fff"/>
    <polygon points="0,880 0,860 1200,790 1200,880" fill="#fff"/>
    <polyline points="760,800 1200,870" stroke="#3276b5" stroke-width="5" fill="none"/>
  </svg>
  <h2>ABOUT <span>HOUSE-SHARE</span></h2>
  <p>Sed ut perspiciatis unde omnis iste natus error sit voluptatem accusantium doloremque laudantium, totam rem aperiam, eaque ipsa quae ab illo inventore veritatis et quasi architecto beatae vitae dicta sunt explicabo. Nemo enim ipsam voluptatem quia voluptas sit aspernatur aut odit aut fugit, sed quia consequuntur magni dolores eos qui ratione voluptatem sequi nesciunt. Neque porro quisquam est, qui dolorem ipsum quia dolor sit amet, consectetur, adipisci velit, sed quia non numquam eius modi tempora incidunt ut labore.</p>
  <div class="btn">Read More
    <svg width="14" height="14" viewBox="0 0 24 24"><circle cx="12" cy="12" r="11" fill="#fff"/><path d="M10 7l5 5-5 5" stroke="#3276b5" stroke-width="3" fill="none"/></svg>
  </div>
  <div class="circle" style="left:690px;top:240px;width:250px;height:250px;background:linear-gradient(160deg,#f1efe9,#c9d8b4 60%,#8d9f6a)" role="img" aria-label="Sunny lounge with green sofa"></div>
  <div class="circle" style="left:905px;top:230px;width:250px;height:250px;background:linear-gradient(160deg,#f4f4f2,#d8d6d2 60%,#5b5b5b)" role="img" aria-label="Modern white kitchen"></div>
  <div class="circle" style="left:795px;top:385px;width:250px;height:250px;background:linear-gradient(160deg,#f6ece6,#d9b8a6 55%,#a98b77)" role="img" aria-label="Living room with pendant lamp and armchairs"></div>
</section>

<!-- portfolio -->
<div class="ghost" style="left:0;top:2575px">PORTFOLIO</div>
<h2 class="heading" style="top:2500px">OUR <span>PORTFOLIO</span></h2>
<div class="heading-rule" style="top:2576px"></div>

<div class="tile" style="left:0;top:2832px;width:272px;height:244px;background:linear-gradient(150deg,#e6e3de,#a7a29b 60%,#6d665f)" role="img" aria-label="Open plan living room with grey sofa"></div>
<div class="tile" style="left:311px;top:2748px;width:272px;height:244px;background:linear-gradient(150deg,#dfe1dd,#7d8a78 55%,#2f3133)" role="img" aria-label="Dark kitchen corner with plants"></div>
<div class="tile" style="left:311px;top:3028px;width:272px;height:244px;background:linear-gradient(150deg,#7aa3d0,#4d83c0 60%,#3a6fa8)" role="img" aria-label="Kitchen interior tinted blue">
  <svg class="zoom" width="70" height="70" viewBox="0 0 70 70"><circle cx="30" cy="30" r="22" fill="none" stroke="#fff" stroke-width="5"/><path d="M46 46l18 18M30 19v22M19 30h22" stroke="#fff" stroke-width="5"/></svg>
</div>
<div class="tile" style="left:618px;top:2680px;width:272px;height:244px;background:linear-gradient(150deg,#f1efeb,#cfcac3 55%,#6f8fa6)" role="img" aria-label="Bright lounge with blue sofa and wall frames"></div>
<div class="tile" style="left:618px;top:2961px;width:272px;height:244px;background:linear-gradient(150deg,#f2f2f0,#565656 50%,#9a9a98)" role="img" aria-label="Grey sofa against a dark feature wall"></div>
<div class="tile" style="left:929px;top:2907px;width:271px;height:236px;background:linear-gradient(150deg,#efe6dd,#c9a58d 55%,#8f6f5a)" role="img" aria-label="Warm lounge with tall windows"></div>

<!-- testimonials -->
<section class="abs testi">
  <div class="testi-photo" role="img" aria-label="Blue tinted background of people at home"></div>
  <div class="ghost">TESTIMONIALS</div>
  <h2 class="heading">CLIENT TESTIMONIALS</h2>
  <div class="heading-rule"></div>
  <div class="abs arrow" style="left:45px"><svg width="14" height="14" viewBox="0 0 24 24"><path d="M15 5l-7 7 7 7" stroke="#fff" stroke-width="3" fill="none"/></svg></div>
  <div class="abs arrow" style="right:45px"><svg width="14" height="14" viewBox="0 0 24 24"><path d="M9 5l7 7-7 7" stroke="#fff" stroke-width="3" fill="none"/></svg></div>
  <div class="card" style="left:118px"><div class="avatar" role="img" aria-label="Client portrait"></div><p>Lorem ipsum dolor sit amet, consectetur adipiscing elit, sed do eiusmod tempoincididunt</p><div class="badge"></div></div>
  <div class="card" style="left:453px"><div class="avatar" role="img" aria-label="Client portrait"></div><p>Lorem ipsum dolor sit amet, consectetur adipiscing elit, sed do eiusmod tempoincididunt</p><div class="badge"></div></div>
  <div class="card" style="left:788px"><div class="avatar" role="img" aria-label="Client portrait"></div><p>Lorem ipsum dolor sit amet, consectetur adipiscing elit, sed do eiusmod tempoincididunt</p><div class="badge"></div></div>
</section>

<!-- newsletter -->
<h2 class="heading" style="top:4370px">SIGN UP <span>NEWSLETTER</span></h2>
<div class="heading-rule" style="top:4448px"></div>
<div class="sub" style="top:4484px;font-size:17px;color:#333">Get the Latest News and Special Offers</div>
<div class="abs input">Enter Email</div>
<div class="abs subscribe">SUBSCRIBE</div>
<div class="sub" style="top:4633px;font-size:11px;color:#777">
  <svg width="10" height="10" viewBox="0 0 10 10" style="vertical-align:-1px;margin-right:6px"><rect x=".5" y=".5" width="9" height="9" fill="#fff" stroke="#999"/></svg>I agree that my submitted data is being collected and stored.
</div>

<!-- contact row -->
<div class="info" style="left:140px">
  <div class="diamond"><svg width="20" height="24" viewBox="0 0 24 30" fill="#3276b5"><path d="M12 0a10 10 0 0 0-10 10c0 8 10 20 10 20s10-12 10-20A10 10 0 0 0 12 0z"/><circle cx="12" cy="10" r="4" fill="#fff"/></svg></div>
  <div>223,Ur enim ad minima veniam,<br>quis nostrum exercitat</div>
</div>
<div class="info" style="left:515px">
  <div class="diamond"><svg width="22" height="22" viewBox="0 0 24 24" fill="#3276b5"><path d="M6.6 10.8a15 15 0 0 0 6.6 6.6l2.2-2.2c.3-.3.7-.4 1-.2 1.1.4 2.3.6 3.6.6.6 0 1 .4 1 1V20c0 .6-.4 1-1 1A17 17 0 0 1 3 4c0-.6.4-1 1-1h3.5c.6 0 1 .4 1 1 0 1.3.2 2.5.6 3.6.1.3 0 .7-.2 1z"/></svg></div>
  <div>Call US : 1 888 888 8888</div>
</div>
<div class="info" style="left:806px">
  <div class="diamond"><svg width="22" height="17" viewBox="0 0 24 18"><rect width="24" height="18" fill="#3276b5"/><path d="M0 0l12 9 12-9" stroke="#fff" stroke-width="2" fill="none"/></svg></div>
  <div>info@companyname.com</div>
</div>

<!-- footer -->
<nav class="abs footer-links">
  <span>HOME</span><i>/</i><span>ABOUT US</span><i>/</i><span>SERVICES</span><i>/</i><span>PORTFOLIO</span><i>/</i><span>NEWS</span><i>/</i><span>CONTACT US</span>
</nav>
<div class="abs footer-bar">© 2019 Companyname All Rights Reserved &nbsp;|&nbsp; Privacy policy</div>

</body>
</html>
```